We need a binder cover. I have attached a photo of what we want it ot look like but use our logo, graphic and colour scheme. The dimensions are”
11.5Hx10.5W – front cover
11.5Hx1.5W – side spine
The Website is www.marbletreeadvisory.ca
For keywords please use Dignity, Independence and Accessibility
As well, we are looking for 2 versions of letterhead .
1. Standard document layout to make table of contents,cover page (no address).
2. Standard letter head with address on the bottom of the page.
Our address is
418 Kestrel Lane East Unit 3 Suite 214
Brackenford Westmere
K9T 4B7
Also want a CD labels for us,
1. With our logo and “Accessibility Standard for Customer Service – Staff Training Session” Power Point with Audio
2. With our logo and “Accessibility Standard for Customer Service – Staff Training Session” CD audio only format
3. With our logo and “ Copy of documentation for QBEX”

```html
<!DOCTYPE html>
<html lang="en">
<head>
<meta charset="utf-8">
<title>Marbletree Advisory – Stationery</title>
<link href="https://fonts.googleapis.com/css2?family=Arimo:wght@400;700&display=swap" rel="stylesheet">
<style>
:root{
  --backdrop:#d8d3cb;
  --paper:#ffffff;
  --ink:#2b2b2b;
  --brand-red:#d6262b;
  --band:#3d3d3f;
  --band-text:#e6e6e6;
  --signature-tone:#e4e4e4;
  --leader:#555555;
}
*{box-sizing:border-box;margin:0;padding:0}
html,body{width:1200px;height:688px;overflow:hidden}
body{background:var(--backdrop);position:relative;font-family:"Arimo",Arial,sans-serif;color:var(--ink)}
.page{position:absolute;top:44px;width:470px;height:616px;background:var(--paper);box-shadow:0 2px 6px rgba(0,0,0,.25)}
.page--contents{left:110px}
.page--letter{left:620px}
.brand{position:absolute;left:30px;top:34px;display:flex;align-items:center;gap:8px}
.brand__mark{width:30px;height:30px;background:var(--brand-red)}
.brand__name{font-size:15px;font-weight:700;line-height:16px;color:var(--brand-red);letter-spacing:.2px}
.page-footer{position:absolute;left:0;right:0;bottom:0;height:16px;background:var(--band);display:flex;justify-content:flex-end;align-items:center}
.page-footer__url{font-size:9px;color:var(--band-text);margin-right:10px}
.page-footer__number{width:16px;height:16px;background:var(--brand-red);color:#fff;font-size:9px;display:flex;align-items:center;justify-content:center;margin-right:28px}

.contents__title{position:absolute;top:108px;left:0;right:0;text-align:center;font-size:12px;font-weight:700}
.contents__list{position:absolute;top:144px;left:38px;right:36px;list-style:none;font-size:8.6px;line-height:11.68px}
.contents__item{display:flex;align-items:baseline;white-space:nowrap}
.contents__item--section{font-weight:700}
.contents__code{width:22px;flex:none}
.contents__leader{flex:1;border-bottom:1px dotted var(--leader);margin:0 4px;transform:translateY(-2px)}
.contents__page{flex:none;font-weight:400}

.letter{position:absolute;top:125px;left:30px;right:30px;font-size:8.8px;line-height:11.3px}
.letter__salutation{margin-bottom:10px}
.letter__body{margin-bottom:11px;text-align:justify}
.letter__signature{width:120px;height:44px;margin-top:6px;background:var(--signature-tone)}
.letter__address{position:absolute;left:30px;bottom:22px;font-size:8.8px;line-height:12px;font-style:normal}
</style>
</head>
<body>

<section class="page page--contents">
  <div class="brand"><span class="brand__mark"></span><span class="brand__name">MARBLETREE<br>ADVISORY INC.</span></div>
  <h1 class="contents__title">TABLE OF CONTENTS</h1>
  <ol class="contents__list">
    <li class="contents__item contents__item--section"><span>SECTION A -- SOLICITATION/CONTRACT FORM</span><span class="contents__leader"></span><span class="contents__page">3</span></li>
    <li class="contents__item"><span class="contents__code">A.1</span><span>GENERAL INFORMATION</span><span class="contents__leader"></span><span class="contents__page">3</span></li>
    <li class="contents__item"><span class="contents__code">A.2</span><span>ISSUING OFFICE</span><span class="contents__leader"></span><span class="contents__page">3</span></li>
    <li class="contents__item"><span class="contents__code">A.3</span><span>RECEIPT OF PROPOSALS AND LATE SUBMISSIONS</span><span class="contents__leader"></span><span class="contents__page">3</span></li>
    <li class="contents__item"><span class="contents__code">A.4</span><span>NOTICE OF SET-ASIDE</span><span class="contents__leader"></span><span class="contents__page">4</span></li>
    <li class="contents__item"><span class="contents__code">A.5</span><span>BASIS FOR AWARD</span><span class="contents__leader"></span><span class="contents__page">4</span></li>
    <li class="contents__item contents__item--section"><span>SECTION B - SUPPLIES OR SERVICES AND PRICES/COSTS</span><span class="contents__leader"></span><span class="contents__page">5</span></li>
    <li class="contents__item"><span class="contents__code">B.1</span><span>SCOPE OF SERVICES</span><span class="contents__leader"></span><span class="contents__page">5</span></li>
    <li class="contents__item"><span class="contents__code">B.2</span><span>CONSIDERATION (FIXED PRICE SERVICES)</span><span class="contents__leader"></span><span class="contents__page">5</span></li>
    <li class="contents__item contents__item--section"><span>SECTION C – DESCRIPTION/SPECIFICATION/WORK STATEMENT</span><span class="contents__leader"></span><span class="contents__page">6</span></li>
    <li class="contents__item"><span class="contents__code">C.1</span><span>BACKGROUND</span><span class="contents__leader"></span><span class="contents__page">6</span></li>
    <li class="contents__item"><span class="contents__code">C.2</span><span>OVERVIEW</span><span class="contents__leader"></span><span class="contents__page">6</span></li>
    <li class="contents__item"><span class="contents__code">C.3</span><span>STATEMENT OF WORK</span><span class="contents__leader"></span><span class="contents__page">6</span></li>
    <li class="contents__item contents__item--section"><span>SECTION D – PACKAGING AND MARKING</span><span class="contents__leader"></span><span class="contents__page">8</span></li>
    <li class="contents__item"><span class="contents__code">D.1</span><span>PACKAGING AND MARKING INSTRUCTIONS</span><span class="contents__leader"></span><span class="contents__page">8</span></li>
    <li class="contents__item contents__item--section"><span>SECTION E -- INSPECTION AND ACCEPTANCE</span><span class="contents__leader"></span><span class="contents__page">9</span></li>
    <li class="contents__item"><span class="contents__code">E.1</span><span>52.252-02 CLAUSES INCORPORATED BY REFERENCE (FEB 1998)</span><span class="contents__leader"></span><span class="contents__page">9</span></li>
    <li class="contents__item"><span class="contents__code">E.2</span><span>ACCEPTANCE OF DELIVERABLES</span><span class="contents__leader"></span><span class="contents__page">9</span></li>
    <li class="contents__item contents__item--section"><span>SECTION F -- DELIVERIES OR PERFORMANCE</span><span class="contents__leader"></span><span class="contents__page">10</span></li>
    <li class="contents__item"><span class="contents__code">F.1</span><span>52.252-02 CLAUSES INCORPORATED BY REFERENCE (FEB 1998)</span><span class="contents__leader"></span><span class="contents__page">10</span></li>
    <li class="contents__item"><span class="contents__code">F.2</span><span>DELIVERY SCHEDULE</span><span class="contents__leader"></span><span class="contents__page">10</span></li>
    <li class="contents__item"><span class="contents__code">F.3</span><span>REPORTING REQUIREMENTS</span><span class="contents__leader"></span><span class="contents__page">10</span></li>
    <li class="contents__item contents__item--section"><span>SECTION G -- CONTRACT ADMINISTRATION DATA</span><span class="contents__leader"></span><span class="contents__page">11</span></li>
    <li class="contents__item"><span class="contents__code">G.1</span><span>INVOICE AND BILLING INFORMATION</span><span class="contents__leader"></span><span class="contents__page">11</span></li>
    <li class="contents__item"><span class="contents__code">G.2</span><span>PAYMENT INFORMATION</span><span class="contents__leader"></span><span class="contents__page">11</span></li>
    <li class="contents__item"><span class="contents__code">G.3</span><span>COTR DESIGNATION AND AUTHORITY</span><span class="contents__leader"></span><span class="contents__page">11</span></li>
    <li class="contents__item"><span class="contents__code">G.4</span><span>CONTRACTING OFFICER'S AUTHORITY</span><span class="contents__leader"></span><span class="contents__page">12</span></li>
    <li class="contents__item"><span class="contents__code">G.5</span><span>CONTRACTOR PERFORMANCE EVALUATIONS</span><span class="contents__leader"></span><span class="contents__page">13</span></li>
    <li class="contents__item contents__item--section"><span>SECTION H – SPECIAL CONTRACT REQUIREMENTS</span><span class="contents__leader"></span><span class="contents__page">14</span></li>
    <li class="contents__item contents__item--section"><span>SECTION I -- CONTRACT CLAUSES</span><span class="contents__leader"></span><span class="contents__page">15</span></li>
    <li class="contents__item"><span class="contents__code">I.1</span><span>52.252-02 CLAUSES INCORPORATED BY REFERENCE (FEB 1998)</span><span class="contents__leader"></span><span class="contents__page">15</span></li>
    <li class="contents__item contents__item--section"><span>SECTION J – LIST OF ATTACHMENTS</span><span class="contents__leader"></span><span class="contents__page">17</span></li>
    <li class="contents__item contents__item--section"><span>SECTION K -- REPRESENTATIONS, CERTIFICATIONS AND OTHER STATEMENTS</span></li>
    <li class="contents__item contents__item--section"><span>OF OFFERORS</span><span class="contents__leader"></span><span class="contents__page">18</span></li>
  </ol>
  <footer class="page-footer"><span class="page-footer__url">www.marbletreeadvisory.ca</span><span class="page-footer__number">1</span></footer>
</section>

<section class="page page--letter">
  <div class="brand"><span class="brand__mark"></span><span class="brand__name">MARBLETREE<br>ADVISORY INC.</span></div>
  <div class="letter">
    <p class="letter__salutation">Mr. Peter Lindqvist,</p>
    <p class="letter__body">Lorem ipsum dolor sit amet, consectetuer adipiscing elit, sed diam nonummy nibh euismod tincidunt ut laoreet dolore magna aliquam erat volutpat. Ut wisi enim ad minim veniam, quis nostrud exerci tation ullamcorper suscipit lobortis nisl ut aliquip ex ea commodo consequat. Duis autem vel eum iriure dolor in hendrerit in vulputate velit esse molestie consequat, vel illum dolore eu feugiat nulla facilisis at vero eros et accumsan et iusto odio dignissim qui blandit praesent luptatum zzril delenit augue duis dolore te feugait nulla facilisi. Nam liber tempor cum soluta nobis eleifend option congue nihil imperdiet doming id quod mazim placerat facer possim assum. Typi non habent claritatem insitam; est usus legentis in iis qui facit eorum claritatem. Investigationes demonstraverunt lectores legere me lius quod ii legunt saepius. Claritas est etiam processus dynamicus, qui sequitur mutationem consuetudium lectorum. Mirum est notare quam littera gothica, quam nunc putamus parum claram, anteposuerit litterarum formas humanitatis per seacula quarta decima et quinta decima. Eodem modo typi, qui nunc nobis videntur parum clari, fiant sollemnes in futurum.</p>
    <p class="letter__body">Lorem ipsum dolor sit amet, consectetuer adipiscing elit, sed diam nonummy nibh euismod tincidunt ut laoreet dolore magna aliquam erat volutpat. Ut wisi enim ad minim veniam, quis nostrud exerci tation ullamcorper suscipit lobortis nisl ut aliquip ex ea commodo consequat. Duis autem vel eum iriure dolor in hendrerit in vulputate velit esse molestie consequat, vel illum dolore eu feugiat nulla facilisis at vero eros et accumsan et iusto odio dignissim qui blandit praesent luptatum zzril delenit augue duis dolore te feugait nulla facilisi. Nam liber tempor cum soluta nobis eleifend option congue nihil imperdiet doming id quod mazim placerat facer possim assum. Typi non habent claritatem insitam; est usus legentis in iis qui facit eorum claritatem. Investigationes demonstraverunt lectores legere me lius quod ii legunt saepius. Claritas est etiam processus dynamicus, qui sequitur mutationem consuetudium lectorum. Mirum est notare quam littera gothica, quam nunc putamus parum claram, anteposuerit litterarum formas humanitatis per seacula quarta decima et quinta decima. Eodem modo typi, qui nunc nobis videntur parum clari, fiant sollemnes in futurum.</p>
    <p>Yours greatful,<br>Jonathan Reyes</p>
    <div class="letter__signature" role="img" aria-label="Handwritten signature"></div>
  </div>
  <address class="letter__address">418 Kestrel Lane East Unit 3 Suite 214<br>Brackenford Westmere, K9T 4B7</address>
  <footer class="page-footer"><span class="page-footer__url">www.marbletreeadvisory.ca</span><span class="page-footer__number">1</span></footer>
</section>

</body>
</html>
```